We are Larkmoor Cardiology and Vascular Medicine and located at 4512 Colby Road, Suites 300 & 400, Brookfield, VA 22990. Our phone is 540-555-0187 We are creating a brochure to promote our Arrhythmia Clinic. Our audience is both patients and referring to help education and understand our arrhythmias. Please add imaging. We appreciate any create suggestions when comes to imaging as long as relates to medical information being provided.

```html
<!DOCTYPE html>
<html lang="en">
<head>
<meta charset="utf-8">
<title>Larkmoor Cardiology – Arrhythmia Clinic Brochure</title>
<link href="https://fonts.googleapis.com/css2?family=Montserrat:wght@400;500;600;700&family=Poppins:wght@500;600;700&display=swap" rel="stylesheet">
<style>
:root{
  --navy:#12283b;
  --teal:#17b490;
  --teal-text:#1fc19b;
  --white:#ffffff;
  --paper:#ffffff;
}
*{box-sizing:border-box;margin:0;padding:0}
html,body{width:1200px;height:777px;overflow:hidden;background:var(--paper)}
body{position:relative;font-family:'Montserrat',sans-serif;color:var(--white)}
.page{position:absolute;width:208px;height:294px;background:var(--navy);overflow:hidden}
.photo{position:absolute;left:0;width:100%}
.page-title{position:absolute;left:0;width:100%;text-align:center;font-family:'Poppins',sans-serif;font-weight:600;font-size:9px;line-height:1.2;color:var(--teal-text);letter-spacing:.2px}
.page-title.light{color:var(--white)}
.footer-band{position:absolute;left:0;bottom:0;width:100%;height:9px;background:var(--teal);color:var(--navy);font-size:3.9px;font-weight:600;letter-spacing:.9px;text-align:center;line-height:9px;text-transform:uppercase;white-space:nowrap}
.term-list{position:absolute;left:21px;right:16px;font-size:4.3px;line-height:1.7;list-style:none}
.term-list li{margin-bottom:6.4px}
.term-list.centered{left:14px;right:14px;text-align:center}
.term{color:var(--teal-text)}
.term.em{font-style:italic}

/* cover */
.cover .practice{position:absolute;top:9px;width:100%;text-align:center;font-size:7.6px;font-weight:500;letter-spacing:2.4px;line-height:1.35}
.cover .kicker{position:absolute;top:61px;width:100%;text-align:center;font-size:7.4px;font-weight:600;letter-spacing:2.4px;color:var(--teal-text)}
.cover .heart{position:absolute;top:74px;left:86px}
.cover h1{position:absolute;top:135px;width:100%;text-align:center;font-family:'Poppins',sans-serif;font-weight:700;font-size:17.5px;line-height:1;letter-spacing:-.4px}
.cover .lede{position:absolute;top:157px;left:24px;right:24px;text-align:center;font-size:6.1px;font-weight:500;line-height:1.55;color:var(--teal-text)}
.cover .info-band{position:absolute;top:205px;left:0;width:100%;height:89px;background:var(--teal);display:flex}
.info-col{flex:1;min-width:0;text-align:center;position:relative}
.info-col svg{display:block;margin:3px auto 0}
.info-col h3{font-size:3.9px;font-weight:700;letter-spacing:.5px;margin-top:6px;white-space:nowrap}
.info-col p{font-size:3.9px;line-height:1.6;margin-top:6px;padding:0 8px}

/* about */
.intro{position:absolute;top:35px;left:22px;right:22px;font-size:3.9px;line-height:1.75;text-align:center}
.symptoms{position:absolute;top:231px;width:100%;text-align:center;font-size:3.6px;font-weight:700;letter-spacing:.6px;line-height:1.4}

/* lifestyle */
.lifestyle{position:absolute;top:218px;left:10px;right:10px;text-align:center;font-size:4.3px;line-height:1.72;list-style:none}

/* procedures */
.procedure-list{position:absolute;top:213px;left:16px;right:16px;text-align:center;font-size:5.1px;line-height:1.6;list-style:none}
.procedure-list li{margin-bottom:6px}

/* back */
.back .mark{position:absolute;top:40px;left:79px}
.back .practice{position:absolute;top:101px;width:100%;text-align:center;font-size:7.8px;font-weight:600;letter-spacing:2.4px;line-height:1.35;color:var(--teal-text)}
.back .contact{position:absolute;top:205px;width:100%;text-align:center;font-size:6.1px;font-weight:600;line-height:1.6}
.back .phone{position:absolute;top:232px;width:100%;text-align:center;font-size:6.1px;font-weight:600}
.back .phone svg{vertical-align:-1px;margin-right:2px}
</style>
</head>
<body>

<!-- Cover -->
<section class="page cover" style="left:25px;top:85px">
  <div class="photo" role="img" aria-label="Woman at a desk holding her chest" style="top:0;height:205px;background:linear-gradient(160deg,#596470 0%,#3d4853 45%,#2b3540 100%)"></div>
  <div class="practice">LARKMOOR CARDIOLOGY<br>AND VASCULAR MEDICINE</div>
  <div class="kicker">ARRHYTHMIAS</div>
  <svg class="heart" width="38" height="32" viewBox="0 0 38 32" aria-hidden="true">
    <path d="M19 31 C4 20 0 14 0 9 C0 3 5 0 9.5 0 C13.5 0 16.5 2 19 5 C21.5 2 24.5 0 28.5 0 C33 0 38 3 38 9 C38 14 34 20 19 31Z" fill="var(--teal)"/>
    <polyline points="4,15 12,15 15,10 18,21 21,7 24,17 26,15 34,15" fill="none" stroke="#fff" stroke-width="1.4" stroke-linejoin="round"/>
  </svg>
  <h1>About Arrhythmias</h1>
  <p class="lede">Arrhythmias are disorders of the electrical system of the heart. A common arrhythmia is atrial fibrillation.</p>
  <div class="info-band">
    <div class="info-col">
      <svg width="30" height="26" viewBox="0 0 30 26" aria-hidden="true" fill="none" stroke="#fff" stroke-width="1">
        <path d="M8 2 C4 4 4 9 6 11 L3 15 L6 16 L6 21 L10 22 L10 25"/>
        <path d="M12 10 L18 7 M12 12 L18 15"/>
        <circle cx="23" cy="11" r="4"/><circle cx="23" cy="11" r="1.6"/>
      </svg>
      <h3>WHAT TO WATCH FOR:</h3>
      <p>Flutters or skipping sensation<br>Racing heart beat<br>Lightheaded spells or passing out<br>Trouble breathing</p>
    </div>
    <div class="info-col">
      <svg width="30" height="26" viewBox="0 0 30 26" aria-hidden="true" fill="none" stroke="#fff" stroke-width="1">
        <circle cx="12" cy="10" r="8.5"/>
        <line x1="18" y1="16" x2="25" y2="24"/>
        <polyline points="5,10 8,10 10,6 12,14 14,8 15,10 19,10"/>
      </svg>
      <h3>HOW TO DIAGNOSE:</h3>
      <p>EKG<br>Heart monitor<br>EP study</p>
    </div>
    <div class="info-col">
      <svg width="30" height="26" viewBox="0 0 30 26" aria-hidden="true" fill="none" stroke="#fff" stroke-width="1">
        <rect x="7" y="3" width="17" height="22" rx="1.5"/>
        <rect x="12" y="1" width="7" height="4" rx="1"/>
        <line x1="10" y1="10" x2="21" y2="10"/><line x1="10" y1="14" x2="21" y2="14"/>
        <line x1="10" y1="18" x2="21" y2="18"/><line x1="10" y1="22" x2="17" y2="22"/>
      </svg>
      <h3>HOW TO TREAT:</h3>
      <p>Medications<br>Lifestyle change<br>Ablation<br>Devices</p>
    </div>
  </div>
</section>

<!-- More about -->
<section class="page" style="left:261px;top:83px">
  <h2 class="page-title" style="top:10px">More about Arrhythmia</h2>
  <p class="intro">Arrhythmia refers to an abnormality of the electrical system of the heart. This may result in the heart beating too fast or too slow or irregularly. If the heart is not beating correctly, then the heart may not pump as strong as it should. This can cause symptoms.</p>
  <div class="photo" role="img" aria-label="Man in a plaid shirt in a park holding his chest" style="top:84px;height:117px;background:linear-gradient(100deg,#6f8a4c 0%,#a8b97a 30%,#8c3b44 60%,#5e7d3e 100%)"></div>
  <h2 class="page-title" style="top:214px;font-size:7px">Symptoms include things such as</h2>
  <div class="symptoms">SKIPS OR FLUTTERS IN THE CHEST.<br>RACING HEART BEAT<br>LIGHTHEADED SPELLS<br>PASSING OUT SPELLS<br>TROUBLE BREATHING</div>
  <div class="footer-band">Larkmoor Cardiology and Vascular Medicine</div>
</section>

<!-- Types -->
<section class="page" style="left:496px;top:85px">
  <div class="photo" role="img" aria-label="Person in a striped shirt with hands clasped over the chest" style="top:0;height:133px;background:linear-gradient(180deg,#6b7886 0%,#56667a 50%,#45566a 100%)"></div>
  <h2 class="page-title light" style="top:16px">Types of arrhythmia include</h2>
  <ul class="term-list" style="top:139px">
    <li><span class="term">Atrial fibrillation:</span> Top half of the heart is beating irregularly</li>
    <li><span class="term">Bradycardia:</span> heart beat is too slow</li>
    <li><span class="term">Conduction disorders:</span> Problems with the electrical cells in the heart</li>
    <li><span class="term">Premature contractions :</span> Early extra heart beats</li>
    <li><span class="term">Tachycardia:</span> abnormally fast heart rate</li>
    <li><span class="term">Supra Ventricular Tachycardia (SVT):</span> Fast abnormal heart beat from the upper heart chambers.</li>
    <li><span class="term">Ventricular Tachycardia:</span> Fast abnormal heart beat from the lower heart chambers</li>
    <li><span class="term">Genetic disorders:</span> Inherited abnormalities in the electrical system that can run in families.</li>
  </ul>
  <div class="footer-band">Larkmoor Cardiology and Vascular Medicine</div>
</section>

<!-- Diagnose -->
<section class="page" style="left:732px;top:85px">
  <div class="photo" role="img" aria-label="Doctor holding a small chalkboard showing a heart" style="top:0;height:99px;background:linear-gradient(90deg,#b9545f 0%,#c9c3c2 45%,#d5d0cf 55%,#b9545f 100%)"></div>
  <h2 class="page-title light" style="top:18px">How to diagnose arrhythmias</h2>
  <ul class="term-list" style="top:112px;left:15px">
    <li><span class="term">EKG:</span>shows the hearts rhythm and electrical pattern at one moment in time</li>
    <li><span class="term">Holter monitor:</span> Wear a monitor that records all your heart’s electrical activity for 1 to 3 days</li>
    <li><span class="term">Event monitor:</span> Wear a monitor for up to a month that records your heart’s activity when you push a button</li>
    <li><span class="term">CTrack:</span> Wear a monitor that records all your heart’s electrical activity for a month</li>
    <li><span class="term">Veritrace:</span> Small implant under the skin that can record all the heart’s electrical activity for a few years.</li>
    <li><span class="term">Tilt Table:</span> Test where blood pressure and heart rate are recorded as you are slowly raised on a table from flat to nearly upright.</li>
    <li><span class="term">EP study:</span> Procedure where an electrical specialist places specialized catheters (small tubes the size of coffee straws) into the heart to analyze the heart’s electrical system.</li>
  </ul>
  <div class="footer-band">Larkmoor Cardiology and Vascular Medicine</div>
</section>

<!-- Treatments -->
<section class="page" style="left:967px;top:85px">
  <h2 class="page-title light" style="top:7px;font-size:10.5px">Treatments</h2>
  <h2 class="page-title" style="top:28px;font-size:9.5px">Life style changes</h2>
  <div class="photo" role="img" aria-label="Woman holding a plank pose on a yoga mat in a sunny room" style="top:63px;height:138px;background:linear-gradient(160deg,#efe4cf 0%,#d9c29b 50%,#c79a55 100%)"></div>
  <ul class="lifestyle">
    <li>Work on ideal weight</li>
    <li>Control blood pressure</li>
    <li>Avoid stimulants (Coffee, tea, caffeinated beverages, chocolate, over the counter stimulants such as pseudophed)</li>
    <li>Limit alcohol consumption</li>
    <li>Exercise</li>
    <li>Treat sleep apnea if present</li>
  </ul>
  <div class="footer-band">Larkmoor Cardiology and Vascular Medicine</div>
</section>

<!-- Medications -->
<section class="page" style="left:25px;top:401px">
  <h2 class="page-title" style="top:12px">Medications</h2>
  <div class="photo" role="img" aria-label="Open hand holding several pills" style="top:38px;height:138px;background:linear-gradient(150deg,#2a2a2c 0%,#4b4240 45%,#a98f86 70%,#2b2b2d 100%)"></div>
  <ul class="term-list" style="top:183px;left:15px">
    <li><span class="term">Beta blockers:</span> Are blood pressure medications that also slow the heart rate down.</li>
    <li><span class="term">Calcium channel blockers:</span> Are blood pressure medications that also slow the heart rate down</li>
    <li><span class="term">Digoxin:</span> Is a medication that can slow the heart rate</li>
    <li><span class="term">Anti-Arrhythmic :</span> Strong medications that work to calm the electrical system of the heart .</li>
    <li><span class="term">Blood thinners:</span> May be used with some arrhythmias such as atrial fibrillation to help reduce the risk for stroke.</li>
  </ul>
  <div class="footer-band">Larkmoor Cardiology and Vascular Medicine</div>
</section>

<!-- Procedures -->
<section class="page" style="left:261px;top:401px">
  <h2 class="page-title" style="top:6px">Procedures</h2>
  <div class="photo" role="img" aria-label="Two clinicians in white coats reviewing a clipboard in a hospital corridor" style="top:34px;height:166px;background:linear-gradient(100deg,#d8d3cc 0%,#eeeae6 40%,#c9c4bd 75%,#b58e6a 100%)"></div>
  <ul class="procedure-list">
    <li><span class="term em">Cardioversion:</span> The patient is put to sleep and the electrical energy is applied to the body to reset the heart rhythm back to normal.</li>
    <li><span class="term em">Ablation:</span> Electrical specialist takes small tubes called catheters up to the heart to find the abnormal rhythm. They then fix the abnormal rhythm by applying high energy to the problem spot which changes that area so that it not longer causes the problem.</li>
  </ul>
  <div class="footer-band">Larkmoor Cardiology and Vascular Medicine</div>
</section>

<!-- Devices -->
<section class="page" style="left:496px;top:401px">
  <h2 class="page-title" style="top:8px">Implantable Devices</h2>
  <div class="photo" role="img" aria-label="Pacemaker and leads on a red surface" style="top:22px;height:135px;background:linear-gradient(130deg,#c61c27 0%,#b9b9b6 30%,#9d9c98 50%,#d02a32 80%,#bf1d26 100%)"></div>
  <ul class="term-list centered" style="top:161px">
    <li><span class="term em">Veritrace Implant:</span> Small monitor implanted under the skin to monitor the heart rhythm for several years.</li>
    <li><span class="term em">Pacemaker:</span> Insertion of a small computer under the skin with wires attached to the heart to prevent the heat from beating too slow.</li>
    <li><span class="term em">Defibrillator:</span> Insertion of a small computer under the skin with wires attached to the heart. This computer watches all the heart beats and “shocks” the heart back to normal if a bad rhythm occurs.</li>
    <li><span class="term em">Cardiac Resynchronization Therapy (CRT):</span> A special type of pacemaker that paces both the left and right side of the heart which can make a weak heart stronger in some circumstances.</li>
    <li><span class="term em">Atriguard Device:</span> Place a plug like device in a part of the heart know as the left atrial appendage to help reduce the risk of stroke from atrial fibrillation.</li>
  </ul>
  <div class="footer-band">Larkmoor Cardiology and Vascular Medicine</div>
</section>

<!-- Back -->
<section class="page back" style="left:732px;top:401px;height:293px">
  <div class="photo" role="img" aria-label="Scattered pills and syringes on a dark surface" style="top:130px;height:163px;background:linear-gradient(180deg,var(--navy) 0%,#23394c 30%,#2c4456 65%,#1e3345 100%)"></div>
  <svg class="mark" width="50" height="50" viewBox="0 0 50 50" aria-hidden="true">
    <circle cx="25" cy="25" r="23" fill="none" stroke="var(--white)" stroke-width="1.2"/>
  </svg>
  <div class="practice">LARKMOOR CARDIOLOGY<br>AND VASCULAR MEDICINE</div>
  <div class="contact">4512 Colby Road, Suites 300 &amp; 400,<br>Brookfield, VA 22990.</div>
  <div class="phone"><svg width="6" height="6" viewBox="0 0 24 24" aria-hidden="true"><path fill="#fff" d="M6.6 10.8a15.1 15.1 0 0 0 6.6 6.6l2.2-2.2c.3-.3.7-.4 1-.2 1.1.4 2.3.6 3.6.6.6 0 1 .4 1 1V20c0 .6-.4 1-1 1A17 17 0 0 1 3 4c0-.6.4-1 1-1h3.5c.6 0 1 .4 1 1 0 1.3.2 2.5.6 3.6.1.3 0 .7-.2 1z"/></svg>540-555-0187</div>
</section>

</body>
</html>
```